RW Holloway LLC Business Card - Civil Engineering & Consulting Firm

We need a Business Card that is elegant, and masculine.  It is our Professional Civil Engineering & Consulting Company located in San Antonio TX (Not s construction or builder firm- no gears & no tool images please). We provide civil engineering services including  commercial site plans, grading and drainage plans, utility plans, hydraulics and hydrology, land planning, utility coordination, and other general civil engineering services related to commercial and residential development.
We have 2 existing Logos. We would like to convey reliability, strength, trustworthiness and attention to detail.  Blues and orange tones as per logo We are OK with the use of a darker blue in the mix.  We have 2 logo versions - Full Company Name Logo to go on the back of card, & Small Icon Logo for the front w/ personal Info.

Target Market(s)
Architects, Real Estate Developers, Other Strctural Engineers, Surveyers, General Contractors
Industry/Entity Type
Professional Civil Engineering
Contact Information for Business Card
Name, Position, Address, Cell & Office #, email, and company website
Font styles to use
Other font styles liked:
- Avian
Requirements
Should not have
- No Tools, No Gears, no Cranes, or Construction Equipment.

```html
<!DOCTYPE html>
<html lang="en">
<head>
<meta charset="utf-8">
<title>RW Holloway LLC – Business Card</title>
<link href="https://fonts.googleapis.com/css2?family=Josefin+Sans:wght@300;400&family=Oswald:wght@500&family=Montserrat:wght@300;400;600&display=swap" rel="stylesheet">
<style>
  :root {
    --navy: #04123a;
    --sky: #7aaedb;
    --orange: #f0922e;
    --white: #f2f4f8;
    --backdrop: #dfe0e0;
  }
  * { margin: 0; padding: 0; box-sizing: border-box; }
  html, body { width: 1200px; height: 1200px; overflow: hidden; }
  body {
    background: var(--backdrop);
    position: relative;
    font-family: "Montserrat", sans-serif;
  }

  /* Back of card: company name */
  .card-back {
    position: absolute;
    left: 29px; top: 411px;
    width: 701px; height: 411px;
    background: var(--navy);
  }
  .card-back .wordmark {
    position: absolute;
    left: 0; right: 0; top: 140px;
    display: flex; flex-direction: column; align-items: center;
  }
  .wordmark .company-name {
    font-family: "Josefin Sans", sans-serif;
    font-weight: 300;
    font-size: 62px;
    letter-spacing: 0.06em;
    color: var(--sky);
    line-height: 1;
  }
  .wordmark .legal-row {
    display: flex; align-items: center; gap: 14px;
    width: 520px; margin-top: 10px;
  }
  .legal-row .rule { flex: 1; height: 2px; background: var(--sky); }
  .legal-row .legal-form {
    font-family: "Josefin Sans", sans-serif;
    font-size: 22px; letter-spacing: 0.2em;
    color: var(--sky); line-height: 1;
  }
  .wordmark .tagline {
    margin-top: 12px;
    font-family: "Josefin Sans", sans-serif;
    font-weight: 400;
    font-size: 20px;
    letter-spacing: 0.32em;
    color: var(--orange);
  }
  .card-back .base-band {
    position: absolute; left: 0; right: 0; bottom: 0; height: 16px;
    background: linear-gradient(to right, var(--orange) 0 188px, var(--sky) 188px 100%);
  }

  /* Front of card: personal details */
  .card-front {
    position: absolute;
    left: 748px; top: 236px;
    width: 412px; height: 701px;
    background: var(--navy);
  }
  .card-front .accent-bar-orange {
    position: absolute; left: 306px; top: 0;
    width: 6px; height: 282px; background: var(--orange);
  }
  .card-front .accent-bar-sky {
    position: absolute; left: 48px; bottom: 0;
    width: 6px; height: 92px; background: var(--sky);
  }
  .card-front .brand-mark {
    position: absolute; left: 230px; top: 282px;
    transform: rotate(-90deg); transform-origin: left top;
    display: flex; align-items: center; gap: 8px;
  }
  .brand-mark .name {
    font-family: "Josefin Sans", sans-serif;
    font-weight: 400; font-size: 20px; letter-spacing: 0.08em;
    color: var(--sky); white-space: nowrap;
  }
  .brand-mark .dot { width: 12px; height: 12px; background: var(--orange); }
  .card-front .website {
    position: absolute; left: 336px; top: 240px;
    transform: rotate(-90deg); transform-origin: left top;
    font-size: 15px; letter-spacing: 0.08em;
    color: var(--white); white-space: nowrap;
  }
  .card-front .web-icon {
    position: absolute; left: 327px; top: 257px;
    width: 25px; height: 25px; background: var(--sky);
    display: flex; align-items: center; justify-content: center;
  }
  .card-front .person {
    position: absolute; left: 78px; top: 352px;
  }
  .person .full-name {
    font-family: "Oswald", sans-serif;
    font-weight: 500; font-size: 36px; line-height: 1;
    color: var(--sky);
  }
  .person .full-name .surname { color: var(--orange); }
  .person .position {
    margin-top: 8px;
    font-size: 15px; color: var(--white); letter-spacing: 0.03em;
  }
  .card-front .contact-list {
    position: absolute; left: 36px; top: 458px;
    list-style: none;
  }
  .contact-list li {
    display: flex; align-items: center; gap: 14px;
    height: 27px; margin-bottom: 10.5px;
    font-size: 17px; font-weight: 300; color: var(--white);
  }
  .contact-list .icon {
    width: 27px; height: 27px; background: var(--orange);
    display: flex; align-items: center; justify-content: center;
    flex: none;
  }
  .contact-list .label { font-weight: 600; color: var(--orange); margin-right: 4px; }
</style>
</head>
<body>

  <section class="card-back" aria-label="Business card back">
    <div class="wordmark">
      <div class="company-name">RW HOLLOWAY</div>
      <div class="legal-row"><span class="rule"></span><span class="legal-form">LLC</span><span class="rule"></span></div>
      <div class="tagline">CONSULTING ENGINEERS</div>
    </div>
    <div class="base-band"></div>
  </section>

  <section class="card-front" aria-label="Business card front">
    <div class="accent-bar-orange"></div>
    <div class="brand-mark"><span class="name">RW HOLLOWAY</span><span class="dot"></span></div>
    <div class="website">WWW.RWHOLLOWAY.COM</div>
    <div class="web-icon">
      <svg width="16" height="16" viewBox="0 0 16 16" fill="none" stroke="#04123a" stroke-width="1.3">
        <circle cx="8" cy="8" r="6.5"/><ellipse cx="8" cy="8" rx="2.8" ry="6.5"/>
        <line x1="1.5" y1="8" x2="14.5" y2="8"/><line x1="2.5" y1="4.5" x2="13.5" y2="4.5"/><line x1="2.5" y1="11.5" x2="13.5" y2="11.5"/>
      </svg>
    </div>

    <div class="person">
      <div class="full-name">NAME <span class="surname">SURNAME</span></div>
      <div class="position">POSITION</div>
    </div>

    <ul class="contact-list">
      <li>
        <span class="icon"><svg width="14" height="16" viewBox="0 0 14 16"><path d="M7 1a5 5 0 0 0-5 5c0 4 5 9 5 9s5-5 5-9a5 5 0 0 0-5-5z" fill="#04123a"/><circle cx="7" cy="6" r="1.8" fill="#f0922e"/></svg></span>
        Address. Building, City ZIP
      </li>
      <li>
        <span class="icon"><svg width="12" height="16" viewBox="0 0 12 16" fill="none" stroke="#04123a" stroke-width="1.4"><rect x="2" y="1" width="8" height="14" rx="1.2"/><line x1="5" y1="12.5" x2="7" y2="12.5"/></svg></span>
        <span><span class="label">M:</span>987 654322</span>
      </li>
      <li>
        <span class="icon"><svg width="16" height="16" viewBox="0 0 16 16"><path d="M4 2l2.5 3-1.5 1.5c.8 1.8 2.2 3.2 4 4L10.5 9l3 2.5-1.5 2.5C7 13.5 2.5 9 2 4z" fill="#04123a"/></svg></span>
        <span><span class="label">O:</span>987 654 321</span>
      </li>
      <li>
        <span class="icon"><svg width="16" height="12" viewBox="0 0 16 12" fill="none" stroke="#04123a" stroke-width="1.4"><rect x="1" y="1" width="14" height="10"/><polyline points="1,1 8,7 15,1"/></svg></span>
        <span><span class="label">E:</span>email@rwholloway.com</span>
      </li>
    </ul>
    <div class="accent-bar-sky"></div>
  </section>

</body>
</html>
```